Conference flyer

We need a flyer for a conference for the defence industry. The attached has been updated with new information using last years flyer. We would like something new and fresh. Please note the theme of the conference is 'a global environment'.

The final design should reflect the defence industry and manufacturing.

Industry/Entity Type

Defence

```html
<!DOCTYPE html>
<html lang="en">
<head>
<meta charset="utf-8">
<title>Defence Trade Controls Conference</title>
<link href="https://fonts.googleapis.com/css2?family=Oswald:wght@400;500;600;700&family=Open+Sans:wght@400;600;700&display=swap" rel="stylesheet">
<style>
  :root {
    --olive: #6e7d2f;
    --olive-dark: #55621f;
    --olive-deep: #3f4a17;
    --rule: #c9cfb3;
    --ink: #333a22;
    --paper: #ffffff;
  }
  * { box-sizing: border-box; margin: 0; padding: 0; }
  html, body { width: 849px; height: 1200px; overflow: hidden; background: var(--paper); }
  body { font-family: "Open Sans", Arial, sans-serif; color: var(--ink); position: relative; }

  .masthead {
    height: 112px;
    background: linear-gradient(180deg, var(--olive) 0%, var(--olive-dark) 100%);
    display: flex; align-items: center; justify-content: center;
  }
  .masthead h1 {
    font-family: "Oswald", "Arial Narrow", sans-serif;
    font-weight: 600; font-size: 46px; letter-spacing: 1px;
    color: #fff; text-transform: uppercase;
  }

  .day-bar {
    margin: 14px 16px 0;
    height: 42px;
    background: var(--olive-deep);
    color: #fff;
    font-family: "Oswald", "Arial Narrow", sans-serif;
    font-weight: 500; font-size: 24px;
    display: flex; align-items: center; padding-left: 14px;
    text-transform: uppercase;
  }

  .schedule {
    margin: 0 16px;
    display: grid; grid-template-columns: 1fr 1fr;
    border-bottom: 2px solid var(--olive);
  }
  .schedule ul { list-style: none; padding: 12px 8px 10px; }
  .schedule ul + ul { border-left: 1px solid var(--rule); padding-left: 18px; }
  .schedule li {
    display: flex; font-size: 14.5px; line-height: 19px; padding: 6px 0;
  }
  .schedule li.sub { padding: 3px 0; }
  .schedule .time { width: 58px; flex: none; font-weight: 600; color: var(--olive-deep); }

  .note { margin: 8px 24px 0; font-size: 12.5px; color: var(--ink); }

  .training-band {
    margin-top: 16px;
    height: 64px;
    background: linear-gradient(180deg, var(--olive) 0%, var(--olive-dark) 100%);
    color: #fff;
    font-family: "Oswald", "Arial Narrow", sans-serif;
    font-weight: 600; font-size: 34px; text-transform: uppercase;
    display: flex; align-items: center; justify-content: center;
  }

  .modules { margin: 0 16px; }
  .modules h2 {
    font-family: "Oswald", "Arial Narrow", sans-serif;
    font-weight: 500; font-size: 21px; color: var(--olive-deep);
    text-transform: uppercase; padding: 18px 10px 10px;
    border-bottom: 2px solid var(--olive);
  }
  .module-row {
    display: flex; align-items: center; padding: 14px 10px;
    border-bottom: 1px solid var(--rule); font-size: 14.5px; line-height: 20px;
  }
  .module-row .when { width: 130px; flex: none; font-weight: 700; color: var(--olive-deep); }
</style>
</head>
<body>
  <header class="masthead">
    <h1>Defence Trade Controls Conference</h1>
  </header>

  <div class="day-bar">Day 1: Tuesday, 2 June 2015</div>
  <section class="schedule">
    <ul>
      <li><span class="time">0830</span>Registration</li>
      <li><span class="time">0900</span>Chair's welcome &amp; opening address</li>
      <li><span class="time">0915</span>Australian Legislative Changes</li>
      <li><span class="time">0950</span>Export Control Reform – next steps</li>
      <li><span class="time">1030</span>Morning tea and networking</li>
      <li><span class="time">1100</span>Managing Multi-jurisdictional Programs</li>
      <li><span class="time">1145</span>Country Focus: Japan</li>
      <li><span class="time">1230</span>Lunch</li>
    </ul>
    <ul>
      <li><span class="time">1330</span>Export Control Reform &amp; FMS,<br>CoA management</li>
      <li><span class="time">1400</span>Country Focus: Singapore</li>
      <li><span class="time">1430</span>Customs Trusted Trader Program</li>
      <li><span class="time">1500</span>Afternoon tea and networking</li>
      <li><span class="time">1530</span>Industry best practice panel,<br>led by the Panel Chair</li>
      <li><span class="time">1645</span>Day one wrap up</li>
      <li><span class="time">1730</span>Reception</li>
    </ul>
  </section>

  <div class="day-bar">Day 2: Wednesday, 3 June 2015</div>
  <section class="schedule">
    <ul>
      <li><span class="time">0900</span>Chair's welcome back</li>
      <li><span class="time">0910</span>Best Practice Compliance</li>
      <li><span class="time">0950</span>Compliance Case Study</li>
      <li><span class="time">1030</span>Morning tea and networking</li>
      <li><span class="time">1100</span>Practical management of export control reform</li>
      <li><span class="time">1130</span>EAR Exceptions – the good, the bad &amp; the ugly</li>
      <li><span class="time">1200</span>Country Focus: European Union</li>
      <li><span class="time">1245</span>Lunch and networking</li>
    </ul>
    <ul>
      <li><span class="time">1345</span>Export Control – round table discussions</li>
      <li class="sub"><span class="time"></span>– Dual national exemptions</li>
      <li class="sub"><span class="time"></span>– Understanding 'Specially Designed'</li>
      <li class="sub"><span class="time"></span>– Deminimis</li>
      <li class="sub"><span class="time"></span>– Re-exports under EAR</li>
      <li class="sub"><span class="time"></span>– U.S. Trade Co-operation Treaty</li>
      <li class="sub"><span class="time"></span>– Securing your supply chain</li>
      <li><span class="time">1500</span>Conference Q&amp;A and wrap-up</li>
      <li><span class="time">1530</span>Conference close</li>
    </ul>
  </section>
  <p class="note">Note: agenda &amp; Presenters may vary without notice</p>

  <div class="training-band">4 x Half Day Pre and Post Training Sessions</div>

  <section class="modules">
    <h2>Pre Conference Training Modules:</h2>
    <div class="module-row"><span class="when">Monday 1 June:</span>Module 1 – Export Controls for Beginners – helping beginners to make the best of the conference</div>
    <h2>Post Conference Training Modules:</h2>
    <div class="module-row"><span class="when">Thursday 4 June:</span>Module 2 – Practical management of export control reform</div>
    <div class="module-row"><span class="when"></span>Module 3 – Tips and Hints for best practice compliance</div>
    <div class="module-row"><span class="when">Friday 5 June:</span>Module 4 – Making the best of Commerce exceptions</div>
  </section>
</body>
</html>
```